Verlindo Magician

I want the business card for my business to give to people who watch that later I will be employed to show magic here is my website http://www.balsamomagicien.com/I want the interesting design , i am very opened for formal and informal, I watch a lot of design so don't stick to the common shape and form but i hope it can also be produced the thing to write on will be the same as in picture that i will upload , i also will upload the logo for you that so can be easy to useDenis CostilleMagicianMAGICIAN BALSAMO 17 rue des Tilleuls - 25000 BESANÇON contact@verlindoillusions.example tel. 0381 946 157 tel. 0674 219 503

```html
<!DOCTYPE html>
<html lang="fr">
<head>
<meta charset="utf-8">
<title>Verlindo Magician — Business Card</title>
<link href="https://fonts.googleapis.com/css2?family=Jost:wght@300;400&display=swap" rel="stylesheet">
<style>
  :root {
    --stage: #e9e6e2;
    --card-dark: #1c1c1d;
    --card-light: #faf8f8;
    --accent: #e3262d;
    --ink-light: #e6e6e6;
    --ink-dark: #151515;
    --rule: #6a6a6a;
    --portrait: #2a2a2a;
  }
  * { box-sizing: border-box; margin: 0; padding: 0; }
  html, body { width: 1125px; height: 1200px; overflow: hidden; }
  body {
    background: var(--stage);
    font-family: "Jost", "Futura", sans-serif;
    font-weight: 300;
    position: relative;
  }
  .card {
    position: absolute;
    left: 150px;
    width: 825px;
    height: 470px;
    box-shadow: 0 3px 8px rgba(0,0,0,0.25);
  }
  .card--front { top: 98px; background: var(--card-dark); color: var(--ink-light); }
  .card--back { top: 631px; background: var(--card-light); }

  .identity {
    position: absolute;
    right: 423px;
    top: 178px;
    text-align: right;
    font-size: 20px;
    line-height: 26px;
  }
  .identity__name {
    color: var(--accent);
    font-size: 31px;
    line-height: 34px;
    font-weight: 400;
    letter-spacing: 0.3px;
  }
  .divider {
    position: absolute;
    left: 425px;
    top: 180px;
    width: 1px;
    height: 112px;
    background: var(--rule);
  }
  .contact {
    position: absolute;
    left: 452px;
    top: 178px;
    list-style: none;
    font-size: 20px;
    line-height: 26px;
    letter-spacing: 0.3px;
  }
  .contact li { display: flex; align-items: center; gap: 10px; }
  .contact svg { width: 16px; height: 16px; fill: var(--accent); flex: none; }

  .portrait {
    position: absolute;
    left: 317px;
    top: 87px;
    width: 191px;
    height: 238px;
    background: linear-gradient(180deg, #3a3a3a 0%, var(--portrait) 60%, #111 100%);
    border-radius: 40px 40px 10px 10px;
  }
  .wordmark {
    position: absolute;
    left: 0;
    right: 0;
    top: 330px;
    text-align: center;
    font-size: 40px;
    font-weight: 300;
    color: var(--ink-dark);
    letter-spacing: 1px;
  }
</style>
</head>
<body>
  <section class="card card--front">
    <div class="identity">
      <p class="identity__name">MARC RAVOULET</p>
      <p>Magician</p>
      <p>MAGICIAN VERLINDO</p>
      <p>17 rue des Tilleuls - 25000 BESANÇON</p>
    </div>
    <div class="divider"></div>
    <ul class="contact">
      <li>
        <svg viewBox="0 0 16 16"><path d="M3.5 1 6 3.8 4.7 5.6c.8 2 2.4 3.6 4.4 4.6l1.8-1.3L14 11.3 12.6 14C7 13.6 2.3 8.9 1.9 3.3z"/></svg>
        0381 946 157
      </li>
      <li>
        <svg viewBox="0 0 16 16"><path d="M3.5 1 6 3.8 4.7 5.6c.8 2 2.4 3.6 4.4 4.6l1.8-1.3L14 11.3 12.6 14C7 13.6 2.3 8.9 1.9 3.3z"/></svg>
        0674 219 503
      </li>
      <li>
        <svg viewBox="0 0 16 16"><path d="M1 3h14v10H1z M1.5 3.5 8 9l6.5-5.5" stroke="#1c1c1d" stroke-width="1.2"/></svg>
        contact@verlindoillusions.example
      </li>
      <li>
        <svg viewBox="0 0 16 16"><circle cx="8" cy="8" r="7"/><path d="M5 4c2 1 1 3 3 3s1 3 3 4M9 2c0 2 2 2 4 3" stroke="#1c1c1d" stroke-width="1.2" fill="none"/></svg>
        www.verlindoillusions.example
      </li>
    </ul>
  </section>

  <section class="card card--back">
    <div class="portrait" role="img" aria-label="Black and white illustration of the magician holding a playing card"></div>
    <p class="wordmark">VERLINDO</p>
  </section>
</body>
</html>
```